MBR - Stationery Design Project

We need stationery based on our logo.

Company info :
Cabinet Voisard & Associés
Société à responsabilité limitée au capital de 200.000 FCFP
RCS Papeete 27586K - Numéro tahiti K73962
Centre d’affaires OPALE - Rue Gaston Perrin
BP 61384 MAHU POTE - 98752 Papeete
Tahiti - Polynésie française
Tél : +689 40 73 16 48
Fax : +689 40 39 64 91

Industry/Entity Type

It Company

Font styles to use
Sans Serif

```html
<!DOCTYPE html>
<html lang="fr">
<head>
<meta charset="utf-8">
<title>MBR – Stationery</title>
<link href="https://fonts.googleapis.com/css2?family=Montserrat:wght@300;400;600&display=swap" rel="stylesheet">
<style>
  :root {
    --navy: #16284a;
    --slate: #8b969c;
    --paper: #ffffff;
    --backdrop: #eceef0;
    --ink: #2b2f36;
    --ink-soft: #6b7078;
    --signature-tint: #e6e9f2;
    --spiral: #9aa3b3;
  }
  * { box-sizing: border-box; margin: 0; padding: 0; }
  html, body { width: 1200px; height: 902px; overflow: hidden; }
  body {
    background: var(--backdrop);
    font-family: "Montserrat", Arial, sans-serif;
    color: var(--ink);
    position: relative;
  }
  .sheet {
    position: absolute;
    background: var(--paper);
    box-shadow: 0 2px 6px rgba(0,0,0,.12);
    overflow: hidden;
  }
  .sheet.navy { background: var(--navy); color: var(--paper); }

  /* Brand lockup */
  .logo { display: inline-flex; flex-direction: column; line-height: 1; }
  .logo-mark { font-weight: 300; letter-spacing: .04em; color: var(--navy); }
  .logo-name { font-weight: 400; color: var(--navy); margin-top: 3px; letter-spacing: .02em; }
  .navy .logo-mark, .navy .logo-name { color: var(--paper); }

  /* Shared footer */
  .sheet-footer {
    position: absolute; font-size: 5.5px; line-height: 1.6; color: var(--ink-soft);
  }
  .edge-band { position: absolute; left: 0; right: 0; bottom: 0; height: 6px; display: flex; }
  .edge-band .navy-part { flex: 0 0 45%; background: var(--navy); }
  .edge-band .slate-part { flex: 1; background: var(--slate); }

  /* Letterhead */
  .letterhead { left: 40px; top: 40px; width: 340px; height: 480px; padding: 34px 32px; }
  .letterhead .logo-mark { font-size: 34px; }
  .letterhead .logo-name { font-size: 8px; }
  .letter-body { margin-top: 38px; font-size: 7px; line-height: 1.6; color: var(--ink-soft); }
  .letter-body .salutation { font-weight: 600; color: var(--ink); font-size: 8px; margin-bottom: 8px; }
  .letter-body p { margin-bottom: 8px; }
  .signature { width: 110px; height: 34px; background: var(--signature-tint); margin: 4px 0 6px; }
  .signatory { font-weight: 600; color: var(--ink); font-size: 8px; }
  .letterhead .sheet-footer { left: 32px; bottom: 26px; }

  /* Folder */
  .folder { left: 405px; top: 40px; width: 340px; height: 480px; display: flex; justify-content: center; padding-top: 60px; }
  .folder .logo { align-items: center; }
  .folder .logo-mark { font-size: 52px; }
  .folder .logo-name { font-size: 11px; }

  /* Envelope back */
  .envelope { left: 775px; top: 40px; width: 385px; height: 210px; }
  .envelope-flap { height: 52px; background: var(--navy); border-radius: 0 0 10px 10px; display: flex; align-items: center; justify-content: center; }
  .envelope-flap .logo-mark { color: var(--paper); font-size: 18px; }

  /* Envelope front */
  .envelope-front { left: 775px; top: 280px; width: 385px; height: 210px; padding: 56px 0 0 44px; }
  .envelope-front .logo-mark { font-size: 38px; }
  .envelope-front .logo-name { font-size: 8px; }
  .envelope-front .sheet-footer { left: 20px; bottom: 18px; }

  /* Business cards */
  .card { width: 250px; height: 145px; }
  .card-front { left: 40px; top: 560px; display: flex; align-items: center; justify-content: center; }
  .card-front.alt { left: 310px; }
  .card-front .logo { align-items: center; }
  .card-front .logo-mark { font-size: 36px; }
  .card-front .logo-name { font-size: 8px; }
  .card-back { left: 40px; top: 725px; }
  .card-back .logo { position: absolute; right: 20px; top: 20px; align-items: flex-end; }
  .card-back .logo-mark { font-size: 26px; }
  .card-back .logo-name { font-size: 6px; }
  .holder { position: absolute; left: 20px; top: 66px; }
  .holder-name { font-size: 8px; font-weight: 600; color: var(--navy); letter-spacing: .05em; }
  .holder-role { font-size: 6px; color: var(--ink-soft); margin-top: 2px; }
  .card-back .sheet-footer { left: 20px; bottom: 14px; font-size: 5px; }

  /* Notebook */
  .notebook { left: 600px; top: 540px; width: 260px; height: 340px; display: flex; justify-content: center; padding-top: 70px; }
  .notebook .logo { align-items: center; }
  .notebook .logo-mark { font-size: 44px; }
  .notebook .logo-name { font-size: 9px; }
  .spiral { position: absolute; left: 0; top: 0; bottom: 0; width: 14px; height: 340px; }

  /* Compliment slip */
  .slip { left: 890px; top: 540px; width: 270px; height: 130px; padding: 22px; }
  .slip .logo-mark { font-size: 28px; }
  .slip .logo-name { font-size: 6px; }
</style>
</head>
<body>

  <section class="sheet letterhead">
    <div class="logo"><span class="logo-mark">MBR</span><span class="logo-name">Cabinet Voisard &amp; Associés</span></div>
    <div class="letter-body">
      <p class="salutation">Dear sir / madame,</p>
      <p>Thank you for your recent enquiry about our services. We are pleased to present the enclosed proposal, prepared by our team after careful review of your needs and goals.</p>
      <p>Please do not hesitate to contact us should you have any questions. We look forward to working with you.</p>
      <p>Yours sincerely,</p>
      <div class="signature" role="img" aria-label="Handwritten signature"></div>
      <p class="signatory">Tania Roux</p>
    </div>
    <div class="sheet-footer">
      Conseil en systèmes d’information<br>
      Études · Intégration · Support<br>
      Société à responsabilité limitée<br>
      Polynésie française
    </div>
    <div class="edge-band"><span class="navy-part"></span><span class="slate-part"></span></div>
  </section>

  <section class="sheet navy folder">
    <div class="logo"><span class="logo-mark">MBR</span><span class="logo-name">Cabinet Voisard &amp; Associés</span></div>
  </section>

  <section class="sheet envelope">
    <div class="envelope-flap"><span class="logo-mark">MBR</span></div>
  </section>

  <section class="sheet envelope-front">
    <div class="logo"><span class="logo-mark">MBR</span><span class="logo-name">Cabinet Voisard &amp; Associés</span></div>
    <div class="sheet-footer">
      Conseil en systèmes d’information · Études · Intégration · Support<br>
      Polynésie française
    </div>
    <div class="edge-band"><span class="slate-part"></span><span class="navy-part"></span></div>
  </section>

  <section class="sheet navy card card-front">
    <div class="logo"><span class="logo-mark">MBR</span><span class="logo-name">Cabinet Voisard &amp; Associés</span></div>
  </section>

  <section class="sheet navy card card-front alt">
    <div class="logo"><span class="logo-mark">MBR</span><span class="logo-name">Cabinet Voisard &amp; Associés</span></div>
  </section>

  <section class="sheet card card-back">
    <div class="logo"><span class="logo-mark">MBR</span><span class="logo-name">Cabinet Voisard &amp; Associés</span></div>
    <div class="holder">
      <p class="holder-name">LÉO MARCHAL</p>
      <p class="holder-role">Managing Director</p>
    </div>
    <div class="sheet-footer">
      Conseil en systèmes d’information<br>
      Études · Intégration · Support
    </div>
    <div class="edge-band"><span class="navy-part"></span><span class="slate-part"></span></div>
  </section>

  <section class="sheet navy notebook">
    <svg class="spiral" viewBox="0 0 14 340" aria-hidden="true">
      <g fill="none" stroke="var(--spiral)" stroke-width="1.5">
        <circle cx="7" cy="20" r="3"/><circle cx="7" cy="40" r="3"/><circle cx="7" cy="60" r="3"/><circle cx="7" cy="80" r="3"/>
        <circle cx="7" cy="100" r="3"/><circle cx="7" cy="120" r="3"/><circle cx="7" cy="140" r="3"/><circle cx="7" cy="160" r="3"/>
        <circle cx="7" cy="180" r="3"/><circle cx="7" cy="200" r="3"/><circle cx="7" cy="220" r="3"/><circle cx="7" cy="240" r="3"/>
        <circle cx="7" cy="260" r="3"/><circle cx="7" cy="280" r="3"/><circle cx="7" cy="300" r="3"/><circle cx="7" cy="320" r="3"/>
      </g>
    </svg>
    <div class="logo"><span class="logo-mark">MBR</span><span class="logo-name">Cabinet Voisard &amp; Associés</span></div>
  </section>

  <section class="sheet slip">
    <div class="logo"><span class="logo-mark">MBR</span><span class="logo-name">Cabinet Voisard &amp; Associés</span></div>
    <div class="edge-band"><span class="navy-part"></span><span class="slate-part"></span></div>
  </section>

</body>
</html>
```